Redesign of business card for Cedar Ridge Mechanical

We are looking for a new design for our business cards for Cedar Ridge Mechanical. We are a plumbing & HVAC construction company, operating on the West Coast of Canada and USA. Logo attached.
Industry/Entity Type
Construction - Plumbing & HVAC
Contact Information for Business Card
Name, address, phone numbers, email, website address
Look and feel
Each slider illustrates characteristics of the customer's brand and the style your logo design should communicate.

```html
<!DOCTYPE html>
<html lang="en">
<head>
<meta charset="utf-8">
<title>Cedar Ridge Mechanical – Business Card</title>
<link href="https://fonts.googleapis.com/css2?family=Montserrat:wght@400;500;700&display=swap" rel="stylesheet">
<style>
  :root {
    --ink: #000000;
    --paper: #ffffff;
    --stripe: #8a8c8d;
    --backdrop: #e6e6e4;
    --card-w: 680px;
    --card-h: 389px;
  }
  * { margin: 0; padding: 0; box-sizing: border-box; }
  html, body {
    width: 1200px;
    height: 900px;
    overflow: hidden;
    background: var(--backdrop);
    font-family: "Montserrat", Arial, sans-serif;
  }
  .canvas {
    width: 1200px;
    height: 900px;
    display: flex;
    flex-direction: column;
    align-items: center;
    justify-content: center;
    gap: 40px;
  }
  .card {
    position: relative;
    width: var(--card-w);
    height: var(--card-h);
    overflow: hidden;
    box-shadow: 0 6px 18px rgba(0,0,0,0.18);
  }

  /* Back side */
  .card--back {
    background: var(--ink);
    display: flex;
    align-items: center;
    justify-content: center;
  }
  .brand {
    display: flex;
    align-items: center;
    gap: 14px;
    font-weight: 700;
    text-transform: uppercase;
    letter-spacing: 0.04em;
  }
  .brand__mark {
    flex: none;
    border: 5px solid currentColor;
  }
  .card--back .brand { color: var(--paper); font-size: 34px; }
  .card--back .brand__mark { width: 40px; height: 40px; }

  /* Front side */
  .card--front { background: var(--paper); color: var(--ink); }
  .card__wave {
    position: absolute;
    inset: 0;
    width: 100%;
    height: 100%;
  }
  .person {
    position: absolute;
    left: 42px;
    top: 58px;
  }
  .person__name {
    font-size: 25px;
    font-weight: 700;
    letter-spacing: 0.02em;
    text-transform: uppercase;
    line-height: 1.1;
  }
  .person__role {
    font-size: 16px;
    font-weight: 400;
    margin-top: 4px;
  }
  .contact {
    position: absolute;
    left: 52px;
    top: 190px;
    list-style: none;
    font-size: 17px;
    line-height: 1.5;
  }
  .contact__item { display: flex; align-items: center; gap: 8px; }
  .contact__icon { width: 14px; height: 14px; flex: none; }
  .contact__address {
    margin-top: 14px;
    margin-left: 22px;
    line-height: 1.35;
  }
  .card--front .brand {
    position: absolute;
    right: 36px;
    top: 62px;
    color: var(--ink);
    font-size: 22px;
  }
  .card--front .brand__mark { width: 28px; height: 28px; border-width: 4px; }
  .website {
    position: absolute;
    right: 38px;
    bottom: 46px;
    color: var(--paper);
    font-size: 15px;
    font-weight: 400;
  }
</style>
</head>
<body>
<main class="canvas">

  <section class="card card--back" aria-label="Card back">
    <div class="brand">
      <span class="brand__mark" aria-hidden="true"></span>
      <span class="brand__name">Cedar Ridge Mechanical</span>
    </div>
  </section>

  <section class="card card--front" aria-label="Card front">
    <svg class="card__wave" viewBox="0 0 680 389" preserveAspectRatio="none" aria-hidden="true">
      <path d="M0 352 C180 350 300 320 420 250 C520 192 600 160 680 150 L680 389 L0 389 Z" fill="#8a8c8d"/>
      <path d="M0 366 C190 364 320 330 440 258 C530 205 610 178 680 170 L680 389 L0 389 Z" fill="#000"/>
    </svg>

    <div class="person">
      <h1 class="person__name">Daniel Hart</h1>
      <p class="person__role">Managing Director</p>
    </div>

    <ul class="contact">
      <li class="contact__item">
        <svg class="contact__icon" viewBox="0 0 24 24" aria-hidden="true"><path fill="#000" d="M6.6 10.8a15.1 15.1 0 0 0 6.6 6.6l2.2-2.2a1 1 0 0 1 1-.25 11.4 11.4 0 0 0 3.6.57 1 1 0 0 1 1 1V20a1 1 0 0 1-1 1A17 17 0 0 1 3 4a1 1 0 0 1 1-1h3.5a1 1 0 0 1 1 1c0 1.25.2 2.45.57 3.57a1 1 0 0 1-.25 1z"/></svg>
        <span>123 456 789</span>
      </li>
      <li class="contact__item">
        <svg class="contact__icon" viewBox="0 0 24 24" aria-hidden="true"><path fill="none" stroke="#000" stroke-width="2.4" d="M3 6h18v12H3z M3 6l9 7 9-7"/></svg>
        <span>info@yourgmail.com</span>
      </li>
      <li class="contact__address">Your address, City<br>State, Zip 1234</li>
    </ul>

    <div class="brand">
      <span class="brand__mark" aria-hidden="true"></span>
      <span class="brand__name">Cedar Ridge Mechanical</span>
    </div>

    <p class="website">www.yourwebsite.com</p>
  </section>

</main>
</body>
</html>
```